Turm7Zwerge
Zielgruppe
Zielgruppe sind die Eltern, Lehrer, Kindergärtner, aber auch Kinder, die bereits Lesen können.
Aufgabenstellung
Ich brauche einen Flyer und ein Plakat für eine Kinderschachschule für Kinder zwischen 4 und 15 Jahren. Auf dem Flyer, den ich in A6-Format drucken möchte (beidseitig), muss ich die Info über die Kinderschachschule Turm7Zwerge (mehr Infos unter www.turm7zwerge-beispiel.ch), dh., was wir machen, Kontaktdaten, etc schreiben können. Es dient als Werbematerial zum Auslegen
Auf dem Plakat wird mehr oder weniger das Gleiche stehen, es wird jedoch als Din A4 Seite aufgehängt.
Unsere Kontaktinformation ist wie folgt:
Turm7Zwerge: Züge für Wolkenkinder
www.turm7zwerge-beispiel.ch

```html
<!DOCTYPE html>
<html lang="de">
<head>
<meta charset="utf-8">
<title>Turm7Zwerge – Kinderschach</title>
<link href="https://fonts.googleapis.com/css2?family=Arimo:ital,wght@0,400;0,700;1,700&family=Chewy&display=swap" rel="stylesheet">
<style>
  :root {
    --band: #c98a1c;
    --blue: #1b8fcb;
    --pink: #d0388e;
    --orange: #f0a21a;
    --ink: #2a2a2a;
    --check: #ececec;
    --white: #ffffff;
  }
  * { margin: 0; padding: 0; box-sizing: border-box; }
  html, body { width: 852px; height: 1200px; overflow: hidden; background: var(--white); }
  .poster {
    position: relative; width: 852px; height: 1200px; overflow: hidden;
    background: var(--white); font-family: "Arimo", Arial, sans-serif; color: var(--ink);
  }
  .board-backdrop { position: absolute; left: 148px; top: 380px; width: 704px; height: 820px; }
  .side-band { position: absolute; left: 0; top: 0; width: 148px; height: 1200px; background: var(--band); }
  .side-url {
    position: absolute; left: 74px; top: 1160px; transform-origin: 0 0; transform: rotate(-90deg) translateY(-50%);
    color: var(--white); font-weight: 700; font-style: italic; font-size: 35px; white-space: nowrap; letter-spacing: 0.5px;
  }
  .brand { position: absolute; right: 55px; top: 70px; text-align: center; }
  .brand-name { font-weight: 700; font-size: 52px; color: var(--pink); line-height: 1; display: flex; align-items: center; gap: 12px; }
  .brand-name .mark { width: 30px; height: 30px; background: var(--ink); }
  .brand-tag { margin-top: 10px; font-weight: 700; font-size: 19px; letter-spacing: 1px; color: var(--ink); }
  .headline {
    position: absolute; left: 172px; top: 222px; color: var(--blue);
    font-weight: 700; font-style: italic; font-size: 33px; line-height: 37px;
  }
  .photo {
    position: absolute; border: 3px solid var(--blue); background: var(--white); padding: 9px;
    box-shadow: 2px 3px 6px rgba(0,0,0,.25);
  }
  .photo .fill { width: 100%; height: 100%; background: linear-gradient(135deg, #3c3226, #8a7a62 45%, #d9d2c4 60%, #4a3a28); }
  .photo-top { left: 30px; top: 395px; width: 360px; height: 228px; transform: rotate(-3deg); }
  .photo-bottom { left: 470px; top: 810px; width: 280px; height: 228px; transform: rotate(-3deg); }
  .slogans { position: absolute; left: 418px; top: 400px; list-style: none; }
  .slogans li {
    display: flex; align-items: center; gap: 14px; height: 54px;
    font-family: "Chewy", cursive; font-size: 42px; color: var(--orange);
    -webkit-text-stroke: 1px #7a4a00;
  }
  .slogans li::before { content: ""; width: 13px; height: 13px; background: var(--pink); transform: rotate(45deg); -webkit-text-stroke: 0; }
  .intro { position: absolute; left: 180px; top: 692px; width: 600px; font-size: 16.5px; line-height: 26px; }
  .benefits { position: absolute; left: 180px; top: 766px; list-style: none; font-size: 17px; }
  .benefits li { display: flex; align-items: center; gap: 14px; height: 30.5px; }
  .benefits li::before { content: ""; width: 9px; height: 9px; background: var(--blue); transform: rotate(45deg); }
  .contact { position: absolute; top: 1072px; font-size: 19.5px; line-height: 31px; }
  .contact-org { left: 180px; }
  .contact-org .org { color: var(--pink); }
  .contact-address { left: 450px; top: 1103px; }
  .contact-reach { left: 632px; top: 1103px; }
</style>
</head>
<body>
<main class="poster">
  <svg class="board-backdrop" viewBox="0 0 704 820" aria-hidden="true">
    <g fill="var(--check)">
      <rect x="40" y="0" width="110" height="100"/><rect x="260" y="0" width="110" height="100"/><rect x="480" y="0" width="110" height="100"/>
      <rect x="150" y="100" width="110" height="110"/><rect x="370" y="100" width="110" height="110"/><rect x="590" y="100" width="114" height="110"/>
      <rect x="40" y="210" width="110" height="120"/><rect x="260" y="210" width="110" height="120"/><rect x="480" y="210" width="110" height="120"/>
      <rect x="150" y="330" width="110" height="130"/><rect x="370" y="330" width="110" height="130"/><rect x="590" y="330" width="114" height="130"/>
      <rect x="40" y="460" width="110" height="140"/><rect x="260" y="460" width="110" height="140"/><rect x="480" y="460" width="110" height="140"/>
      <rect x="150" y="600" width="110" height="160"/><rect x="370" y="600" width="110" height="160"/><rect x="590" y="600" width="114" height="160"/>
    </g>
  </svg>

  <aside class="side-band"></aside>
  <div class="side-url">www.turm7zwerge-beispiel.ch</div>

  <header class="brand">
    <div class="brand-name"><span class="mark"></span>Turm7Zwerge</div>
    <div class="brand-tag">ZÜGE FÜR WOLKENKINDER</div>
  </header>

  <h1 class="headline">Kinderschach:<br>Wir bringen Ihr Kind<br>Zug um Zug zum Erfolg!</h1>

  <figure class="photo photo-top"><div class="fill" role="img" aria-label="Foto: zwei Kinder spielen Schach an einem Brett"></div></figure>

  <ul class="slogans">
    <li>Schach macht Spaß!</li>
    <li>Schach macht stark!</li>
    <li>Schach macht schlau!</li>
  </ul>

  <p class="intro">Wir bieten täglich hochwertige kindgerechte Schachkurse für Kinder ab 4 Jahren an. Unser Schachtraining beinhaltet:</p>
  <ul class="benefits">
    <li>Konzentrationstraining</li>
    <li>Vertrauensaufbau</li>
    <li>Stärkung des Selbstvertrauens</li>
    <li>Persönliches Wachstum</li>
    <li>Geistige Herausforderung</li>
    <li>Intelektuelle Stärkung</li>
  </ul>

  <figure class="photo photo-bottom"><div class="fill" role="img" aria-label="Foto: Kinder beim Schachspiel"></div></figure>

  <address class="contact contact-org" style="font-style:normal"><span class="org">Turm7Zwerge</span><br>Züge für Wolkenkinder<br>Bea Malvik, Präsidentin</address>
  <address class="contact contact-address" style="font-style:normal">Lindenpfad 12<br>8799 Seewil</address>
  <address class="contact contact-reach" style="font-style:normal">Tel.: 079-0000 1 23<br>info@turm7zwerge-beispiel.ch</address>
</main>
</body>
</html>
```